I need a label with logo to go on jars of honey.
Label size 70mm x 70mm
The front label should say :
The Fenwick Honey Co. (logo)
Tarapeka Honey
400g
The back label:
Would have nutritional information
And our address
You can see from the uploaded files the styles I prefer, I have uploaded a photo of the honey product too. The background of the logo doesn't have to be white. I would like to develop a color scheme that would look nice against the color of the honey.
Logo Text
The Fenwick Honey Co. / The Fenwick Honey Company

```html
<!DOCTYPE html>
<html lang="en">
<head>
<meta charset="UTF-8">
<title>The Fenwick Honey Co. – Jar Label</title>
<link rel="stylesheet" href="https://fonts.googleapis.com/css2?family=Mali:wght@400;600&display=swap">
<style>
  :root {
    --page-bg: #ffffff;
    --label-fill: #f1f1b9;
    --label-rim: #9a8a7e;
    --ink: #7a6248;
  }
  html, body {
    margin: 0;
    padding: 0;
    width: 1016px;
    height: 1200px;
    overflow: hidden;
    background: var(--page-bg);
  }
  .canvas {
    position: relative;
    width: 1016px;
    height: 1200px;
    display: flex;
    align-items: center;
    justify-content: center;
  }
  .label {
    width: 620px;
    height: 620px;
    box-sizing: border-box;
    border-radius: 50%;
    background: var(--label-fill);
    border: 11px solid var(--label-rim);
    display: flex;
    flex-direction: column;
    align-items: center;
    justify-content: center;
    color: var(--ink);
    font-family: "Mali", "Comic Sans MS", cursive;
    text-align: center;
  }
  .brand-name {
    margin: 0;
    font-weight: 600;
    font-size: 56px;
    line-height: 1.05;
    letter-spacing: 0.5px;
  }
  .brand-dot {
    width: 120px;
    height: 120px;
    margin: 28px 0 30px;
    border-radius: 50%;
    border: 5px solid var(--ink);
    box-sizing: border-box;
  }
  .product-name {
    margin: 0;
    font-weight: 400;
    font-size: 40px;
    line-height: 1.1;
  }
  .net-weight {
    margin: 6px 0 0;
    font-weight: 400;
    font-size: 30px;
    line-height: 1.1;
  }
</style>
</head>
<body>
  <main class="canvas">
    <section class="label" aria-label="Front jar label">
      <h1 class="brand-name">The Fenwick<br>Honey Co.</h1>
      <div class="brand-dot" aria-hidden="true"></div>
      <p class="product-name">Tarapeka Honey</p>
      <p class="net-weight">400g</p>
    </section>
  </main>
</body>
</html>
```